Vibrant, yet professional, stationery set and other designs required.

I need to source a fantastic designer for a new project as part of my company using a new logo designed via sketch harbor.

**UPDATE** I am not looking for just 'fine' design that will suffice. I am looking for something great.

We are a life assurance brokerage based in Dublin, Ireland and BrightRoost.ie is our new website aimed at providing services for young families in Ireland. We are hoping to be the 'Velro' level of service providers in this area and I am looking for the quality of design to reflect this :-) Hopefully that makes sense!

I have a preference for straight lines over curves and waves.

I need...

1. Business card
2. Letterhead
3. Banner (for printing - 76cm X 305cm)
4. Car branding for KORVA 9 (2014 sport model) I believe the templates are freely available online.

Target Market(s)

Parents in Ireland - Aged 27 to 50.

Industry/Entity Type

Financial Planning

Colors

Designer to choose colors to be used in the design.

Requirements
Must have
• All of the items listed in the description above. I like clean, bright, legible, vibrant and professional design.
Should not have
• No silly or 'cheap' looking designs. This is a professional company looking to provide a professional service.

```html
<!DOCTYPE html>
<html lang="en">
<head>
<meta charset="utf-8">
<title>BrightRoost.ie — Business Card</title>
<link rel="stylesheet" href="https://fonts.googleapis.com/css2?family=Roboto:wght@400;500;700&family=Roboto+Condensed:wght@500;700&display=swap">
<style>
  :root {
    --backdrop: #ecebe8;
    --card-grey: #8a9699;
    --card-white: #f7f7f6;
    --brand-orange: #f0821e;
    --brand-grey: #8a9699;
    --ink: #4a4a4a;
    --white: #ffffff;
  }
  * { margin: 0; padding: 0; box-sizing: border-box; }
  html, body {
    width: 1200px; height: 960px; overflow: hidden;
    background: var(--backdrop);
    font-family: "Roboto", Arial, sans-serif;
  }
  .canvas { position: relative; width: 1200px; height: 960px; }

  .card {
    position: absolute; left: 320px; width: 600px; height: 342px;
    box-shadow: 0 2px 6px rgba(0,0,0,0.18);
  }

  /* Front */
  .card-front { top: 106px; background: var(--card-grey); }
  .card-front .wordmark {
    position: absolute; left: 0; right: 0; top: 128px;
    text-align: center; color: var(--white);
    font-weight: 500; font-size: 62px; letter-spacing: -1px; line-height: 1;
  }
  .card-front .web {
    position: absolute; left: 0; right: 0; top: 288px;
    text-align: center; color: var(--white);
    font-size: 14px; letter-spacing: 6.5px;
  }

  /* Back */
  .card-back { top: 493px; background: var(--card-white); }
  .name-band {
    position: absolute; left: 0; top: 54px; width: 350px; height: 50px;
    background: var(--brand-orange); color: var(--white);
    font-family: "Roboto Condensed", Arial, sans-serif;
    padding: 5px 0 0 29px;
  }
  .name-band .name { font-weight: 700; font-size: 20px; line-height: 24px; }
  .name-band .role { font-weight: 500; font-size: 15px; line-height: 18px; }

  .card-back .logo {
    position: absolute; right: 28px; top: 62px;
    display: flex; align-items: center; gap: 8px;
    color: var(--brand-grey);
    font-weight: 500; font-size: 34px; letter-spacing: -0.5px; line-height: 1;
  }
  .card-back .logo .dot {
    width: 14px; height: 14px; border-radius: 50%; background: var(--brand-orange);
  }

  .contacts {
    position: absolute; left: 29px; top: 238px; list-style: none;
    color: var(--ink); font-size: 14px;
  }
  .contacts li { display: flex; align-items: center; height: 19px; }
  .contacts svg { width: 14px; height: 14px; margin-right: 8px; fill: var(--brand-orange); }

  .address {
    position: absolute; right: 28px; top: 259px;
    text-align: right; color: var(--ink); font-size: 14px; line-height: 18.5px;
  }
  .address .web { letter-spacing: 1px; }
</style>
</head>
<body>
<main class="canvas">

  <section class="card card-front" aria-label="Business card front">
    <div class="wordmark">BrightRoost.ie</div>
    <div class="web">www.brightroost.ie</div>
  </section>

  <section class="card card-back" aria-label="Business card back">
    <div class="name-band">
      <div class="name">Liam Byrne</div>
      <div class="role">CEO/Founder</div>
    </div>

    <div class="logo"><span class="dot"></span>BrightRoost.ie</div>

    <ul class="contacts">
      <li>
        <svg viewBox="0 0 16 16" aria-hidden="true"><path d="M3.6 1.2l2.3 2.6-1.3 2c.9 1.9 2.3 3.3 4.2 4.3l2-1.3 2.6 2.3-1.4 2.3C6.6 13.9 2.1 9.4 1.3 2.6z"/></svg>
        614 208 3571
      </li>
      <li>
        <svg viewBox="0 0 16 16" aria-hidden="true"><path d="M4.5 1h7v14h-7zM6 2.5v9.5h4V2.5zM7.3 13h1.4v1.2H7.3z" fill-rule="evenodd"/></svg>
        872 519 4406
      </li>
      <li>
        <svg viewBox="0 0 16 16" aria-hidden="true"><path d="M4 1.5h8v4H4zM1 6.5h14v6h-2.5v2.5h-9v-2.5H1zM5 11v2.5h6V11z" fill-rule="evenodd"/></svg>
        453 770 1285
      </li>
      <li>
        <svg viewBox="0 0 16 16" aria-hidden="true"><path d="M1 3.5h14v1.2L8 9 1 4.7zM1 6.2l7 4.3 7-4.3v6.3H1z"/></svg>
        hello@brightroost.ie
      </li>
    </ul>

    <div class="address">
      <div>4210 Alder Row</div>
      <div>Kilmory, Dublin D07 K4R2</div>
      <div class="web">www.brightroost.ie</div>
    </div>
  </section>

</main>
</body>
</html>
```